Generate website for parcelnook.com

Please design a website for our business. It must be clean, streamlined and obvious.

Our business combines ecommerce, with social networking, and zorvi maps. The logo is a shopping bag (ecommerce) and honeycombs inside representing the various compartments of business that are offered throughout site.

Clients use our site to visit the interior of stores and restaurants through video streaming and can virtually "walk through" the store and purchase items with friends and loved ones through the web.

We want to incorporate this logo with the work that we are doing and play on this honeycomb theme.

Our business is "parcelnook.com" because we are all about "u"!

Please make homepage with about us tab, contact us form, mission tab, we also want a page with our research links included that bolster the case for our startup.

We will incorporate a small video on the front screen. A homepage like fildrawer.com only this time with our parcelnook!

Also include, COMING SOON, on the homepage please.
Updates

These are some good templates/example sites of clean and simple but effective: https://7elmrow.com/preview www.fildrawer.com

We are excited to see your submissions. Currently, a very good and only one designer has posted so far. Let us know!

Please include the TM (trademark) symbol after the logo, the name, and the slogan throughout the website. Thank you!

Put the TM after the LOGO and after the slogan "Placement ran Supreme" Lorcan

Target Market(s)

We will begin with female online shoppers.

Industry/Entity Type

Shopping

Font styles to use
Serif
Sans Serif

Colors
e567a6
fece3e
85cae6

Requirements
Must have
• Clean Look
Simple like Fildrawer with simple options "see film" or login/signup.

With browser tabs at the bottom much like fildrawer.

1. Shopper when opening Parcelnook.com website will see a simple webpage with a large Parcelnook logo in the center.

2. User will see log-in and password or create account in upper right hand corner of webpage. Mobile device website will be underneath logo.

3.We Prefer a background for webpages adding a softer experience on the the eyes of the user. A photo in the background to show shopretail experience.

4. Clicking on theParcelnook logo will inform users of details and instructions about platform. Example: About, contact, mission, Help etc. Logo will become somewhat like an interactive tool for help and guidance.

5. Parcelnook is currently scouting for it's founding venues. A founding venue will be the first venues to appear to the public on the Parcelnook platform. Founding venues (FV) will inherit a lifetime of the lowest possible rates of 2%* for the duration of it's business. All businesses wishing to participate in the founding venues offer please leave your email address and store name and a representative will get back with you.

*Venues will be subjected to credit card and CoinTrail rates in addition.

Nice to have
• http://www.zorvi.com/patents/US5193774

Must include the link above/visual of this page on the site as well.

```html
<!DOCTYPE html>
<html lang="en">
<head>
<meta charset="utf-8">
<title>Parcelnook</title>
<link rel="stylesheet" href="https://fonts.googleapis.com/css2?family=Jost:wght@400;500;600&family=Arimo:wght@400&display=swap">
<style>
:root{
  --ink:#000000;
  --paper:#ffffff;
  --veil:rgba(255,255,255,0.62);
  --wood-light:#e9c98f;
  --wood-mid:#c99a5a;
  --floor-shade:#9c7b52;
  --glass:#d9d4cc;
  --button-top:#ff9c8c;
  --button-bottom:#f4655a;
  --brand:#e567a6;
}
*{margin:0;padding:0;box-sizing:border-box}
html,body{width:1200px;height:1091px;overflow:hidden;background:var(--ink)}
.page{position:relative;width:1200px;height:1091px;overflow:hidden;font-family:"Jost",sans-serif}
.site-nav{position:absolute;left:0;top:0;width:1200px;height:136px;background:var(--ink)}
.site-nav a{position:absolute;top:56px;color:var(--paper);font-family:"Arimo",sans-serif;font-size:20px;text-decoration:none}
.hero-photo{position:absolute;left:0;top:136px;width:1200px;height:819px;
  background:linear-gradient(180deg,var(--glass) 0%,var(--wood-light) 30%,var(--wood-mid) 70%,var(--floor-shade) 100%)}
.intro-band{position:absolute;left:0;top:255px;width:1200px;height:516px;background:var(--veil);box-shadow:0 2px 3px rgba(0,0,0,0.35)}
.brand-name{position:absolute;left:0;width:1200px;top:362px;text-align:center;font-size:68px;font-weight:600;color:var(--brand);letter-spacing:-1px}
.brand-mark{display:inline-block;width:34px;height:34px;border-radius:50%;background:var(--brand);margin-right:18px;vertical-align:middle;position:relative;top:-6px}
.tagline{position:absolute;left:0;width:1200px;top:443px;text-align:center;font-size:25px;color:var(--ink)}
.column-title{position:absolute;width:420px;text-align:center;font-size:35px;line-height:52px;color:var(--paper);text-shadow:0 2px 4px rgba(0,0,0,0.55)}
.divider{position:absolute;left:616px;top:504px;width:2px;height:243px;background:var(--paper)}
.enroll-box{position:absolute;top:611px;width:379px;height:141px;border:2px solid var(--paper);border-radius:10px}
.enroll-label{position:absolute;left:0;top:8px;width:100%;text-align:center;font-size:28px;color:var(--paper);text-shadow:0 2px 4px rgba(0,0,0,0.55)}
.email-button{position:absolute;top:50px;width:252px;height:66px;border-radius:3px;
  background:linear-gradient(180deg,var(--button-top),var(--button-bottom));box-shadow:2px 3px 5px rgba(0,0,0,0.45);
  color:var(--paper);font-family:"Jost",sans-serif;font-size:23px;text-align:center;line-height:64px;border:none}
.site-footer{position:absolute;left:0;top:955px;width:1200px;height:136px;background:var(--ink);color:var(--paper);text-align:center}
.offer{position:absolute;left:0;width:1200px;font-family:"Arimo",sans-serif;font-size:20px}
.footer-rule{position:absolute;left:63px;top:82px;width:1096px;height:1px;background:#8a8a8a}
.legal{position:absolute;left:0;top:94px;width:1200px;font-size:13.5px;font-weight:500}
</style>
</head>
<body>
<div class="page">
  <nav class="site-nav">
    <a style="left:131px" href="#about">About us</a>
    <a style="left:389px" href="#mission">Mission</a>
    <a style="left:692px" href="#coming-soon">Coming soon</a>
    <a style="left:972px" href="#contact">Contact us</a>
  </nav>

  <div class="hero-photo" role="img" aria-label="Overhead view of a multi-level clothing store with wooden floors, escalators and shoppers walking the aisles"></div>

  <section class="intro-band">
  </section>
  <div class="brand-name"><span class="brand-mark"></span>Parcelnook</div>
  <div class="tagline">Shop and walk with friends through the aisles</div>

  <h2 class="column-title" style="left:166px;top:500px">Sign up to join the experience</h2>
  <h2 class="column-title" style="left:645px;top:500px">Request or Become a participating store</h2>
  <div class="divider"></div>

  <div class="enroll-box" style="left:188px">
    <div class="enroll-label">Enroll here to shop</div>
    <div class="email-button" style="left:60px">Enter email adresse</div>
  </div>
  <div class="enroll-box" style="left:659px">
    <div class="enroll-label">Enroll or nominate a shop</div>
    <div class="email-button" style="left:63px">Enter email adresse</div>
  </div>

  <footer class="site-footer">
    <div class="offer" style="top:16px">Founding venues will inherit a 2% lifetime fee*</div>
    <div class="offer" style="top:48px">Limited to a select few</div>
    <div class="footer-rule"></div>
    <div class="legal">©2014 · Parcelnook.com LLC. All rights reserved. Under authorized use of patent #5193774 Uspto</div>
  </footer>
</div>
</body>
</html>
```